Velk Partners Building Business Cards

We need a business card that reflects our business as "Solar Experts" in San Diego. Browse our website www.velkpartners.example our License needs to be displayed as "CSLB# 3867140" our phone number is (619) 555-0187

Save thousands on your electric bills and increase the value of your home while helping to protect the environment. Our solar installation experts will help you design the system that's right for you, using only the highest quality equipment that will look great and give you ideal performance. Our goal is to make you energy independent, and get your electric bill to 0.

Paul Osterby
(619) 555-0187
paul@velkpartners.example

Target Market(s)

Home owners in san diego looking for solar

Industry/Entity Type

Solar Energy

Contact Information for Business Card

Paul Osterby
(619) 555-0187
paul@velkpartners.example

Font styles to use
Other font styles liked:
• Use our logo font

Requirements
Must have
• License needs to be displayed as "CSLB# 3867140" our phone number is (619) 555-0187
Nice to have
• Real images of rooftop home solar in san diego
Should not have
• our business address

```html
<!DOCTYPE html>
<html lang="en">
<head>
<meta charset="utf-8">
<title>Velk Partners Building – Business Card</title>
<link href="https://fonts.googleapis.com/css2?family=Open+Sans:wght@400;600;700&display=swap" rel="stylesheet">
<style>
  :root {
    --page-bg: #e9e7e4;
    --card-bg: #f3f2f0;
    --card-edge: #d9d7d3;
    --navy: #1f2c55;
    --navy-deep: #141d3d;
    --navy-light: #2c3d6e;
    --orange: #e8891e;
    --text-light: #e6e9f2;
    --text-muted: #c9cedc;
  }
  * { box-sizing: border-box; margin: 0; padding: 0; }
  html, body {
    width: 1200px;
    height: 969px;
    overflow: hidden;
    background: var(--page-bg);
    font-family: "Open Sans", Arial, sans-serif;
  }
  .business-card {
    position: absolute;
    left: 150px;
    top: 228px;
    width: 900px;
    height: 512px;
    background: var(--card-bg);
    border: 1px solid var(--card-edge);
    box-shadow: 0 10px 30px rgba(0,0,0,0.12);
  }
  .company-name {
    position: absolute;
    left: 0;
    right: 0;
    top: 96px;
    text-align: center;
    font-weight: 700;
    font-size: 58px;
    letter-spacing: -0.5px;
    color: var(--navy);
  }
  .contact-band {
    position: absolute;
    left: 39px;
    top: 284px;
    width: 830px;
    height: 209px;
    background: linear-gradient(100deg, var(--navy-deep) 0%, var(--navy-light) 40%, var(--navy) 70%, var(--navy-deep) 100%);
    border: 2px solid var(--orange);
  }
  .crop-marks {
    position: absolute;
    left: 0;
    top: 0;
    width: 900px;
    height: 512px;
    pointer-events: none;
  }
  .person {
    position: absolute;
    right: 458px;
    top: 62px;
    text-align: right;
  }
  .person-name {
    font-weight: 700;
    font-size: 32px;
    color: var(--orange);
    line-height: 1.2;
  }
  .person-title {
    font-size: 24px;
    color: var(--text-light);
    line-height: 1.35;
  }
  .divider {
    position: absolute;
    left: 372px;
    top: 28px;
    width: 1px;
    height: 150px;
    background: rgba(230,233,242,0.45);
  }
  .contact-list {
    position: absolute;
    left: 418px;
    top: 26px;
    list-style: none;
    font-size: 24px;
    color: var(--text-light);
    line-height: 36px;
  }
  .contact-list li {
    display: flex;
    align-items: center;
    gap: 12px;
  }
  .contact-list .license {
    color: var(--text-muted);
    margin-bottom: 8px;
  }
  .contact-icon {
    width: 20px;
    height: 20px;
    flex: none;
  }
</style>
</head>
<body>
  <div class="business-card">
    <div class="company-name">Velk Partners Building</div>

    <div class="contact-band">
      <div class="person">
        <div class="person-name">Paul Osterby</div>
        <div class="person-title">CEO/Founder</div>
      </div>
      <div class="divider"></div>
      <ul class="contact-list">
        <li class="license">CSLB# 3867140</li>
        <li>
          <svg class="contact-icon" viewBox="0 0 20 20" aria-hidden="true">
            <path d="M4 2 L7.5 2 L9 6 L7 7.5 C8 10 10 12 12.5 13 L14 11 L18 12.5 L18 16 C18 17 17 18 16 18 C8.5 17.5 2.5 11.5 2 4 C2 3 3 2 4 2 Z" fill="var(--orange)"/>
          </svg>
          (619) 555-0187
        </li>
        <li>
          <svg class="contact-icon" viewBox="0 0 20 20" aria-hidden="true">
            <rect x="1" y="4" width="18" height="12" fill="var(--orange)"/>
            <path d="M1.5 4.5 L10 11 L18.5 4.5" fill="none" stroke="var(--navy)" stroke-width="1.5"/>
          </svg>
          paul@velkpartners.example
        </li>
        <li>
          <svg class="contact-icon" viewBox="0 0 20 20" aria-hidden="true">
            <circle cx="10" cy="10" r="8.5" fill="var(--orange)"/>
            <path d="M1.5 10 H18.5 M10 1.5 C6 6 6 14 10 18.5 M10 1.5 C14 6 14 14 10 18.5" fill="none" stroke="var(--navy)" stroke-width="1.2"/>
          </svg>
          www.velkpartners.example
        </li>
      </ul>
    </div>

    <svg class="crop-marks" viewBox="0 0 900 512" aria-hidden="true">
      <g stroke="var(--orange)" stroke-width="1.5" fill="none">
        <path d="M39 268 V284 M22 285 H39"/>
        <path d="M869 268 V284 M869 285 H886"/>
        <path d="M39 493 V508 M22 492 H39"/>
        <path d="M869 493 V508 M869 492 H886"/>
      </g>
    </svg>
  </div>
</body>
</html>
```